Business card for my new company (Accounting firm)

I need a business card for my new business Brightwell Advisory and Ledger SA. Our services are accounting, tax, audit and financial management. Our customers are small companies, start-ups and new companies. The final design has to show financial security, trust and growth. Please find our logo attached to the business card. Text for the business card: Brightwell Advisory and Ledger SA Tomas Varenholt Director and Founder Certified Accountant Tel. 022 418 57 34 tv@clairevalconseil.ch www.clairevalconseil.ch Rue des Vergières 27 1201 Geneva
Target Market(s)
Our customers are small companies, start-ups and new companies.
Industry/Entity Type
Finance And Accounting
Contact Information for Business Card
Claireval Conseil et Comptes SA
Tomas Varenholt
Directeur et Fondateur
Expert-comptable diplômé
Tél. 022 418 57 34
tv@clairevalconseil.ch
www.clairevalconseil.ch
Rue des Vergières 27
1201 Genève

```html
<!DOCTYPE html>
<html lang="fr">
<head>
<meta charset="utf-8">
<title>Claireval Conseil et Comptes SA — Carte de visite</title>
<link href="https://fonts.googleapis.com/css2?family=Roboto:wght@400;500;700&display=swap" rel="stylesheet">
<style>
  :root {
    --bg: #e4e5e7;
    --blue-light: #2ea3d6;
    --blue-mid: #1f86bd;
    --blue-deep: #1d5f8e;
    --ink: #3a3c3f;
    --ink-soft: #55585c;
    --paper: #f4f4f4;
    --white: #ffffff;
  }
  * { margin: 0; padding: 0; box-sizing: border-box; }
  html, body { width: 1200px; height: 726px; overflow: hidden; background: var(--bg); }
  body { font-family: 'Roboto', sans-serif; position: relative; }

  .card {
    position: absolute;
    top: 195px;
    width: 520px;
    height: 336px;
    border-radius: 4px;
    box-shadow: 0 10px 28px rgba(0,0,0,0.12);
  }

  /* Front side */
  .card-front {
    left: 50px;
    background: linear-gradient(160deg, var(--blue-light) 0%, var(--blue-mid) 55%, var(--blue-deep) 100%);
    color: var(--white);
    display: flex;
    flex-direction: column;
    align-items: center;
    justify-content: center;
  }
  .front-name {
    font-weight: 500;
    font-size: 30px;
    letter-spacing: 3px;
    text-transform: uppercase;
    text-align: center;
    line-height: 1.25;
  }
  .front-web {
    margin-top: 46px;
    font-weight: 500;
    font-size: 15px;
    letter-spacing: 0.5px;
  }

  /* Back side */
  .card-back {
    left: 630px;
    background: var(--paper);
  }
  .brand {
    position: absolute;
    left: 34px;
    top: 190px;
    display: flex;
    align-items: flex-start;
    gap: 10px;
  }
  .brand-square {
    width: 16px;
    height: 16px;
    background: var(--blue-deep);
    margin-top: 4px;
  }
  .brand-name {
    font-weight: 500;
    font-size: 18px;
    line-height: 1.3;
    letter-spacing: 1.5px;
    text-transform: uppercase;
    color: var(--ink);
  }

  .contact {
    position: absolute;
    left: 290px;
    top: 40px;
    color: var(--ink-soft);
  }
  .person-name {
    font-weight: 700;
    font-size: 19px;
    color: var(--blue-deep);
  }
  .person-role {
    font-size: 11.5px;
    line-height: 1.35;
    margin-top: 4px;
  }
  .contact-list {
    list-style: none;
    margin-top: 22px;
    font-size: 12.5px;
    line-height: 1.55;
  }
  .contact-list li { display: flex; align-items: center; gap: 9px; }
  .contact-list svg { width: 11px; height: 11px; fill: var(--blue-deep); flex: none; }
  .address {
    margin-top: 14px;
    padding-left: 20px;
    font-size: 12.5px;
    line-height: 1.45;
  }
</style>
</head>
<body>

  <section class="card card-front" aria-label="Recto de la carte">
    <p class="front-name">Claireval<br>Conseil et Comptes</p>
    <p class="front-web">www.clairevalconseil.ch</p>
  </section>

  <section class="card card-back" aria-label="Verso de la carte">
    <div class="brand">
      <span class="brand-square"></span>
      <p class="brand-name">Claireval<br>Conseil et Comptes</p>
    </div>

    <div class="contact">
      <h1 class="person-name">Tomas Varenholt</h1>
      <p class="person-role">Directeur et Fondateur<br>Expert-comptable diplômé</p>

      <ul class="contact-list">
        <li>
          <svg viewBox="0 0 24 24" aria-hidden="true"><path d="M6.6 10.8a15.1 15.1 0 0 0 6.6 6.6l2.2-2.2a1 1 0 0 1 1-.25 11.4 11.4 0 0 0 3.6.57 1 1 0 0 1 1 1V20a1 1 0 0 1-1 1A17 17 0 0 1 3 4a1 1 0 0 1 1-1h3.5a1 1 0 0 1 1 1c0 1.25.2 2.45.57 3.57a1 1 0 0 1-.25 1z"/></svg>
          022 418 57 34
        </li>
        <li>
          <svg viewBox="0 0 24 24" aria-hidden="true"><path d="M2 5h20v14H2z M2 5l10 8 10-8" fill="none" stroke="currentColor"/><path d="M2 5h20v2l-10 7L2 7z"/><path d="M2 9l10 7 10-7v10H2z"/></svg>
          tv@clairevalconseil.ch
        </li>
        <li>
          <svg viewBox="0 0 24 24" aria-hidden="true"><path d="M12 2a10 10 0 1 0 0 20 10 10 0 0 0 0-20zm6.9 6h-2.9a15.7 15.7 0 0 0-1.4-3.6A8 8 0 0 1 18.9 8zM12 4c.8 1.2 1.5 2.5 1.9 4h-3.8c.4-1.5 1.1-2.8 1.9-4zM4.3 14a8 8 0 0 1 0-4h3.4a16 16 0 0 0 0 4zm.8 2h2.9a15.7 15.7 0 0 0 1.4 3.6A8 8 0 0 1 5.1 16zM8 8H5.1a8 8 0 0 1 4.3-3.6A15.7 15.7 0 0 0 8 8zm4 12c-.8-1.2-1.5-2.5-1.9-4h3.8c-.4 1.5-1.1 2.8-1.9 4zm2.3-6H9.7a14 14 0 0 1 0-4h4.6a14 14 0 0 1 0 4zm.3 5.6A15.7 15.7 0 0 0 16 16h2.9a8 8 0 0 1-4.3 3.6zM16.3 14a16 16 0 0 0 0-4h3.4a8 8 0 0 1 0 4z"/></svg>
          www.clairevalconseil.ch
        </li>
      </ul>

      <p class="address">Rue des Vergières 27<br>1201 Genève</p>
    </div>
  </section>

</body>
</html>
```